Flyer Design Print Ad for Clothing Store

We are a modest women's clothing store. We are looking for a print ad 90*134 mm that is attention grabbing and can serve as a template for us going forward. We cannot use pictures of actual women. We need it to include our logo, store hours, physical address, website, phone number. We would use this template and change the call to action as necessary e. g. BOGO Sale, 30% off, flash sale, summer sale etc. Our colors are black and white and our fonts are Bodoni sans and Athens.

Target Market(s)

Women from teen to age 70

Industry/Entity Type

Women's clothing

Font styles to use
Other font styles liked:
• Athens, Bodoni Sans

Requirements
Must have
• Our, logo, phone number, website, address and store hours
Nice to have
• I'd like something that's not just our flat logo but something that will make someone pause to look
Should not have
• Pictures of women

```html
<!DOCTYPE html>
<html lang="en">
<head>
<meta charset="utf-8">
<title>Lorewyn – Summer Sale</title>
<link rel="stylesheet" href="https://fonts.googleapis.com/css2?family=Italiana&family=Tenor+Sans&family=Heebo:wght@400&display=swap">
<style>
  :root {
    --ink: #131821;
    --gold: #fdc26e;
    --white: #ffffff;
    --cloth-cream: #e9d3b8;
    --cloth-red: #d9595a;
    --cloth-orange: #f39a3a;
  }
  * { margin: 0; padding: 0; box-sizing: border-box; }
  html, body { width: 848px; height: 1200px; overflow: hidden; background: var(--ink); }
  .flyer {
    position: relative; width: 848px; height: 1200px; overflow: hidden;
    background: var(--ink); font-family: "Tenor Sans", sans-serif;
  }
  .brand { position: absolute; top: 58px; left: 0; width: 848px; text-align: center; }
  .brand-dot {
    display: block; width: 92px; height: 92px; margin: 0 auto;
    border-radius: 50%; background: var(--white);
  }
  .brand-name {
    display: block; margin-top: 16px; color: var(--white);
    font-family: "Tenor Sans", sans-serif; font-size: 24px; letter-spacing: 9px;
    padding-left: 9px;
  }
  .headline { position: absolute; left: 0; top: 0; width: 848px; height: 420px; font-weight: 400; }
  .headline-small {
    position: absolute; left: 40px; top: 294px; color: var(--gold);
    font-family: "Italiana", serif; font-size: 72px; line-height: 1;
    transform: skewX(-10deg); letter-spacing: 1px;
  }
  .headline-big {
    position: absolute; left: 316px; top: 220px; color: var(--gold);
    font-family: "Italiana", serif; font-size: 210px; line-height: 1;
    letter-spacing: 14px;
  }
  .photo-rack {
    position: absolute; left: 290px; top: 420px; width: 558px; height: 780px;
    background: linear-gradient(90deg, var(--cloth-cream) 0%, #cdb498 25%, var(--cloth-red) 32%, #e9b3b0 48%, var(--cloth-orange) 55%, #f7a345 90%, #efe4e6 100%);
    clip-path: polygon(0 21%, 40% 0, 100% 0, 100% 100%, 0 100%);
  }
  .photo-rack-far {
    position: absolute; left: 0; top: 585px; width: 310px; height: 367px;
    background: linear-gradient(90deg, #4a3d3f 0%, #6b4a34 30%, #6b3e40 70%, #2d2b33 100%);
    opacity: 0.8;
  }
  .info {
    position: absolute; left: 0; top: 952px; width: 339px; height: 248px;
    background: var(--ink); color: var(--gold);
  }
  .info-phone { position: absolute; left: 29px; top: 28px; font-size: 21px; letter-spacing: 1.2px; }
  .info-hours { position: absolute; left: 31px; top: 68px; font-size: 15.5px; line-height: 21.5px; letter-spacing: 0.6px; }
  .info-address { position: absolute; left: 31px; top: 139px; font-size: 12.5px; line-height: 16px; white-space: nowrap; }
  .info-address .he { font-family: "Heebo", sans-serif; direction: rtl; unicode-bidi: isolate; display: inline-block; }
  .web {
    position: absolute; left: 429px; top: 1129px; width: 330px; height: 46px;
    background: var(--ink); color: var(--gold); text-align: center;
    font-size: 17px; letter-spacing: 5px; line-height: 46px; padding-left: 5px;
  }
</style>
</head>
<body>
<main class="flyer">
  <header class="brand">
    <span class="brand-dot"></span>
    <span class="brand-name">LOREWYN</span>
  </header>

  <h1 class="headline">
    <span class="headline-small">SUMMER</span>
    <span class="headline-big">SALE</span>
  </h1>

  <div class="photo-rack-far" role="img" aria-label="Dimmed rack of hanging blouses and dresses in the background"></div>
  <div class="photo-rack" role="img" aria-label="Clothing rack with cream knit cardigans, red polka-dot dresses and orange ruffled blouses on dark hangers"></div>

  <section class="info">
    <p class="info-phone">PHONE ; 077-5550142</p>
    <p class="info-hours">WORKING HOUR<br>S-TH- 10:30-12:30 - <span dir="rtl">א-ה</span><br>20:30 - 22:30</p>
    <p class="info-address">
      <span class="he">מרכז מסחרי גבעת ארזים</span><br>
      CEDAR HILL SHOPPING CENTER<br>
      <span class="he">(מעל המאפייה)</span><br>
      <span class="he">ניתן להגיע גם משדרות הארזים 8</span><br>
      BUSES 14, 18, 27, 33, 40, 47, 56, 61, 73, 80, 84
    </p>
  </section>

  <p class="web">WWW.LOREWYN.CO.IL</p>
</main>
</body>
</html>
```